Wordpress Design for a Digital Management Consulting Business

I need a simple Wordpress Design and someone to set it up for a new boutique management consulting business called Quillon Advisory that specialises in providing strategic advice to help grow digital businesses. It covers business strategy, marketing strategy, digital strategy, web product development, marketing campaigns, social, search, etc. From strategy to implementation.

URL is: quillonadvisory.com.au

My professional background is here: au.linkedin.com/in/hollyprenwick

Competitors: other boutique digital/marketing management consulting businesses in Australia

The logos, colours and fonts are attached.

I would like the site to convey a business that is Smart/intelligent, Contemporary, Progressive, Digital, Energetic, Friendly.

The objective of the site is to educate visitors about what Quillon Advisory does and encourage them to contact me for more information. It will be very light on content.

Target Market(s)

CEOs/Managing Directors, General Managers, Marketing Directors

Industry/Entity Type

Management Consulting

Font styles to use
Sans Serif

Colors
e34197
5c5c5c
000000

Requirements
Must have
• Site design requirements:
• Choose an appropriate Wordpress template, set it up for me and let me be able to edit it ongoing.
• It should use lots of images - these can be inspirational and not necessarily tied directly to the work
• Pink should feature, but not be the dominant colour.
• Site structure should be:
• 1. Home page - image led with horizontal navigation. Text beneath and images to describe the services.
• 2. About page - with space to write text and insert a picture of the Director
• 3. Services - with space to highlight services either as a list or graphically with text
• 4. Contact page - with space to write text and add email links, etc.
• Should have horizontal navigation
• It should have the flexibility to add another page
Nice to have
• Use the tree icon somehow in the design - consider in the background enlarged
• Use pink, grey, black from logo. Can introduce another complimentary colour if necessary.
• Can introduce another complimentary font to go with the logo font.
Should not have
• Use cliched business images and icons, eg. business suits, hand shakes, business men, business ties.

```html
<!DOCTYPE html>
<html lang="en">
<head>
<meta charset="utf-8">
<title>Quillon Advisory</title>
<link href="https://fonts.googleapis.com/css2?family=Open+Sans:wght@300;400;600;700&family=Raleway:wght@300;400;600;800&display=swap" rel="stylesheet">
<style>
:root{
  --pink:#e34197;
  --pink-dark:#c92f80;
  --grey:#5c5c5c;
  --grey-light:#8a8a8a;
  --line:#dcdcdc;
  --black:#000;
  --footer:#161616;
  --footer-text:#b5b5b5;
  --white:#fff;
}
*{margin:0;padding:0;box-sizing:border-box}
html,body{width:1200px;height:2292px;overflow:hidden;background:var(--white)}
body{font-family:"Open Sans",Arial,sans-serif;color:var(--grey);position:relative}

/* header */
.site-header{position:absolute;top:0;left:0;width:1200px;height:72px;display:flex;align-items:center;justify-content:space-between;padding:0 40px 0 36px;background:var(--white)}
.brand{display:flex;align-items:center;gap:14px}
.brand-mark{width:34px;height:34px;border-radius:50%;background:var(--pink)}
.brand-name{font-family:"Raleway",sans-serif;font-weight:400;font-size:30px;color:var(--pink);letter-spacing:1px}
.main-nav{display:flex;gap:6px}
.main-nav a{font-family:"Raleway",sans-serif;font-size:14px;font-weight:600;color:var(--grey);text-decoration:none;padding:8px 22px;letter-spacing:.5px}
.main-nav a.current{color:var(--pink);border-bottom:3px solid var(--pink)}

/* hero */
.hero{position:absolute;top:72px;left:0;width:1200px;height:560px}
.hero-photo{position:absolute;inset:0;background:linear-gradient(90deg,#c9b8a6 0%,#dcd3c9 30%,#eceae7 55%,#f3f3f3 100%)}
.hero-copy{position:absolute;left:720px;top:150px;width:420px}
.hero-title{font-family:"Raleway",sans-serif;font-weight:800;font-size:72px;line-height:1;color:var(--pink);letter-spacing:2px}
.hero-sub{font-family:"Raleway",sans-serif;font-weight:800;font-size:17px;color:#333;margin-top:8px;letter-spacing:.5px}
.hero-text{font-size:14px;line-height:1.5;color:var(--grey);margin-top:12px;width:380px}
.btn-dark{display:inline-block;background:#333;color:var(--white);font-size:14px;padding:12px 26px;border-radius:3px;text-decoration:none}
.hero .btn-dark{position:absolute;left:112px;top:332px}
.slider-dots{position:absolute;left:0;right:0;bottom:30px;display:flex;justify-content:center;gap:8px}
.slider-dots span{width:12px;height:12px;border-radius:50%;background:#666}
.slider-dots span.on{background:#222}

/* section headings */
.section-heading{display:flex;align-items:center;justify-content:center;gap:20px;font-family:"Raleway",sans-serif;font-weight:600;font-size:24px;letter-spacing:2px;color:var(--pink)}
.section-heading::before,.section-heading::after{content:"";width:150px;height:1px;background:var(--line)}

/* who we are */
.who{position:absolute;top:660px;left:0;width:1200px;text-align:center}
.who-text{width:1140px;margin:28px auto 0;text-align:left;font-size:16px;line-height:1.55;color:var(--grey-light)}
.who .btn-dark{margin-top:34px;background:#444;padding:14px 30px}

/* services */
.services{position:absolute;top:1000px;left:0;width:1200px;height:600px;background:var(--pink)}
.services .section-heading{color:var(--white);margin-top:60px}
.services .section-heading::before,.services .section-heading::after{background:rgba(255,255,255,.5)}
.service-grid{display:flex;justify-content:space-between;padding:0 64px;margin-top:40px}
.service{width:280px;text-align:center;color:var(--white)}
.service-img{width:280px;height:162px;border:4px solid var(--white)}
.service-img.a{background:linear-gradient(135deg,#2f3a4a,#7f8fa6)}
.service-img.b{background:linear-gradient(135deg,#e7edf2,#9fb7c9)}
.service-img.c{background:linear-gradient(135deg,#3a4a6b,#b8c6dc)}
.service h3{font-family:"Raleway",sans-serif;font-weight:800;font-size:20px;margin-top:22px;letter-spacing:.5px}
.service p{font-size:14px;line-height:1.45;margin:12px auto 0;width:230px}
.btn-light{display:inline-block;margin-top:24px;background:var(--white);color:#222;font-size:14px;padding:9px 20px;border-radius:3px;text-decoration:none}

/* what we do */
.what{position:absolute;top:1600px;left:0;width:1200px;height:372px}
.what .section-heading{margin-top:46px}
.what-grid{display:flex;justify-content:space-between;padding:0 40px;margin-top:34px}
.what-item{width:340px;text-align:center}
.what-icon{width:96px;height:96px;margin:0 auto}
.what-item h3{font-family:"Open Sans",sans-serif;font-weight:400;font-size:20px;color:#222;margin-top:12px}
.what-item p{font-size:14px;line-height:1.45;color:var(--grey);width:240px;margin:10px auto 0}

/* footer */
.site-footer{position:absolute;top:1972px;left:0;width:1200px;height:320px;background:var(--footer);color:var(--footer-text)}
.foot-col{position:absolute;top:34px}
.foot-col h4{font-family:"Raleway",sans-serif;font-weight:400;font-size:22px;color:var(--white);margin-bottom:28px}
.foot-col ul{list-style:none}
.foot-col li{font-size:13px;margin-bottom:14px;padding-left:14px;position:relative}
.foot-col li::before{content:"›";position:absolute;left:0;color:var(--pink)}
.col-links{left:64px}
.col-services{left:256px}
.col-services .lists{display:flex;gap:70px}
.col-follow{left:720px;width:120px;height:250px;border-left:1px solid #333;border-right:1px solid #333;padding-left:20px}
.social{display:flex;flex-direction:column;gap:12px}
.social span{width:34px;height:34px;border-radius:50%;background:#3a3a3a}
.col-contact{left:880px;width:290px}
.col-contact p{font-size:13px;line-height:1.5}
.contact-line{display:flex;align-items:center;gap:10px;margin-top:12px;font-size:13px}
.contact-line .dot{width:22px;height:22px;border-radius:50%;background:var(--pink);display:flex;align-items:center;justify-content:center}
</style>
</head>
<body>

<header class="site-header">
  <div class="brand"><span class="brand-mark"></span><span class="brand-name">Quillon Advisory</span></div>
  <nav class="main-nav">
    <a class="current" href="#">HOME</a><a href="#">ABOUT US</a><a href="#">SERVICES</a><a href="#">PROJECTS</a><a href="#">NEWS</a><a href="#">CONTACT</a>
  </nav>
</header>

<section class="hero">
  <div class="hero-photo" role="img" aria-label="Photo of a smiling man in a bright office"></div>
  <div class="hero-copy">
    <h1 class="hero-title">ACHIEVE</h1>
    <p class="hero-sub">YOUR GOALS AND LONG TERM SUCCESS</p>
    <p class="hero-text">Clear strategy turns ambition into measurable growth. We help digital businesses plan, launch and scale with confidence and focus.</p>
    <a class="btn-dark" href="#">Read More</a>
  </div>
  <div class="slider-dots"><span class="on"></span><span></span><span></span><span></span></div>
</section>

<section class="who">
  <h2 class="section-heading">WHO WE ARE</h2>
  <p class="who-text">Quillon Advisory is a boutique management consulting company advising digital businesses across business, product and marketing strategy. Combining strategic thinking with digital knowhow and marketing expertise Quillon Advisory works with businesses looking to develop their digital capabilities or wanting to accelerate the growth of a new or existing digital business.</p>
  <a class="btn-dark" href="#">Click to know more...</a>
</section>

<section class="services">
  <h2 class="section-heading">OUR SERVICES</h2>
  <div class="service-grid">
    <div class="service">
      <div class="service-img a" role="img" aria-label="Image of hands working with digital screens"></div>
      <h3>DIGITAL STRATEGY</h3>
      <p>Shape a clear roadmap for your online channels, products and platforms that drives growth.</p>
      <a class="btn-light" href="#">Read More</a>
    </div>
    <div class="service">
      <div class="service-img b" role="img" aria-label="Image of a marketing plan sketched on a whiteboard"></div>
      <h3>MARKETING STRATEGY</h3>
      <p>Position your brand, reach the right audience and turn campaigns into lasting customer value.</p>
      <a class="btn-light" href="#">Read More</a>
    </div>
    <div class="service">
      <div class="service-img c" role="img" aria-label="Image of a person touching a digital interface"></div>
      <h3>DIGITAL TRANSFORMATION</h3>
      <p>Modernise systems, teams and processes so your business is ready for the next digital step.</p>
      <a class="btn-light" href="#">Read More</a>
    </div>
  </div>
</section>

<section class="what">
  <h2 class="section-heading">WHAT WE DO</h2>
  <div class="what-grid">
    <div class="what-item">
      <svg class="what-icon" viewBox="0 0 96 96"><circle cx="48" cy="48" r="46" fill="var(--pink)"/><circle cx="48" cy="42" r="16" fill="none" stroke="#fff" stroke-width="4"/><rect x="40" y="60" width="16" height="5" fill="#fff"/><rect x="42" y="68" width="12" height="4" fill="#fff"/></svg>
      <h3>Strategic Thinking</h3>
      <p>We look beyond the obvious to find the ideas that move your business forward.</p>
    </div>
    <div class="what-item">
      <svg class="what-icon" viewBox="0 0 96 96"><circle cx="48" cy="48" r="46" fill="var(--pink)"/><rect x="28" y="52" width="9" height="18" fill="#fff"/><rect x="43" y="40" width="9" height="30" fill="#fff"/><rect x="58" y="28" width="9" height="42" fill="#fff"/></svg>
      <h3>Analytical Approach</h3>
      <p>Decisions grounded in data, research and market insight rather than guesswork or habit.</p>
    </div>
    <div class="what-item">
      <svg class="what-icon" viewBox="0 0 96 96"><circle cx="48" cy="48" r="46" fill="var(--pink)"/><polyline points="30,50 43,63 67,35" fill="none" stroke="#fff" stroke-width="6" stroke-linecap="round" stroke-linejoin="round"/></svg>
      <h3>End to End Project Management</h3>
      <p>From first workshop to final launch, we stay with you until the job is done.</p>
    </div>
  </div>
</section>

<footer class="site-footer">
  <div class="foot-col col-links">
    <h4>Quick Links</h4>
    <ul><li>Home</li><li>About Us</li><li>Projects</li><li>News</li><li>Contacts</li></ul>
  </div>
  <div class="foot-col col-services">
    <h4>Services</h4>
    <div class="lists">
      <ul><li>Business Strategy</li><li>Digital Strategy</li><li>Marketing Strategy</li><li>Product Strategy</li><li>Marketing Campaigns</li></ul>
      <ul><li>Product Management</li><li>Digital Marketing</li><li>Sales CRM Strategy</li><li>Content Marketing</li><li>New Product Launches</li></ul>
    </div>
  </div>
  <div class="foot-col col-follow">
    <h4>Follow Us</h4>
    <div class="social"><span></span><span></span><span></span></div>
  </div>
  <div class="foot-col col-contact">
    <h4>Contact Details</h4>
    <p>For more information about what we do, please contact:</p>
    <p style="margin-top:10px;color:#fff">Holly Prenwick</p>
    <div class="contact-line"><span class="dot"><svg width="12" height="12" viewBox="0 0 12 12"><path d="M3 1l2 3-1.5 1.2a7 7 0 0 0 3.3 3.3L8 7l3 2-1 2C5 11 1 7 1 2z" fill="#fff"/></svg></span>0412 558 903</div>
    <div class="contact-line"><span class="dot"><svg width="12" height="12" viewBox="0 0 12 12"><rect x="1" y="3" width="10" height="7" fill="none" stroke="#fff"/><polyline points="1,3 6,7 11,3" fill="none" stroke="#fff"/></svg></span>info@quillonadvisory.com.au</div>
  </div>
</footer>

</body>
</html>
```